Unique Business Card Design

Unique Business Card design for our orthotic and prosthetic company. Our logo is on our website, color is light blue. Unique shape (artificial leg shaped, vertical, etc..) preferred. Logo, business name, individual name and basic demographics needed.

Industry/Entity Type

Business

Contact Information for Business Card

Logo, Industry, Phone # Logo, "Prosthetic & Orthotic Services" Place to add individual name and contact info

Colors
cee9f5

Requirements
Must have
• The icon must be there, placement of "Prosthetic & Orthotic Services" can be moved
Nice to have
• Like the mix of light blue, and a little darker blue. One design included the icons from my website which was a nice touch

```html
<!DOCTYPE html>
<html lang="en">
<head>
<meta charset="utf-8">
<title>Limbworks Inc. Business Card</title>
<link rel="stylesheet" href="https://fonts.googleapis.com/css2?family=Open+Sans:wght@400;600&family=Crimson+Text:ital@1&display=swap">
<style>
  :root {
    --brand-blue: #165ea8;
    --paper: #ffffff;
    --ink: #3a3a3a;
    --backdrop: #e8ebee;
  }
  * { margin: 0; padding: 0; box-sizing: border-box; }
  html, body { width: 1200px; height: 812px; overflow: hidden; background: var(--backdrop); font-family: "Open Sans", sans-serif; }
  .canvas { position: relative; width: 1200px; height: 812px; }
  .card { position: absolute; width: 525px; height: 300px; top: 256px; box-shadow: 0 6px 18px rgba(0,0,0,.12); overflow: hidden; }

  /* Back side */
  .card-back { left: 50px; background: var(--brand-blue); color: var(--paper); }
  .back-mark { position: absolute; left: 50%; top: 44px; transform: translateX(-50%); width: 190px; height: 150px; border-radius: 50%; background: var(--paper); display: flex; align-items: center; justify-content: center; }
  .back-mark-name { color: var(--brand-blue); font-weight: 600; font-size: 17px; letter-spacing: 1px; }
  .back-url { position: absolute; left: 0; right: 0; top: 226px; text-align: center; font-size: 14px; letter-spacing: 5px; }

  /* Front side */
  .card-front { left: 625px; background: var(--paper); }
  .side-band { position: absolute; left: 20px; top: 0; width: 120px; height: 100%; background: var(--brand-blue); }
  .band-mark { position: absolute; left: 14px; top: 30px; width: 92px; height: 92px; border-radius: 50%; border: 2px solid var(--paper); display: flex; align-items: center; justify-content: center; color: var(--paper); font-weight: 600; font-size: 11px; letter-spacing: .5px; }
  .icon { position: absolute; left: 92px; width: 14px; height: 14px; fill: var(--paper); }

  .company { position: absolute; left: 160px; top: 34px; }
  .company-name { color: var(--brand-blue); font-size: 25px; font-weight: 600; letter-spacing: .5px; border-bottom: 2px solid var(--brand-blue); padding-bottom: 2px; line-height: 1.1; }
  .company-tagline { color: var(--brand-blue); font-family: "Crimson Text", serif; font-style: italic; font-size: 14px; margin-top: 2px; }

  .contact { position: absolute; left: 160px; top: 130px; color: var(--ink); font-size: 13px; }
  .contact-name { color: var(--brand-blue); font-size: 19px; line-height: 24px; margin-bottom: 6px; }
  .contact-name strong { font-weight: 600; }
  .contact-name .credentials { font-size: 13px; }
  .contact-line { line-height: 20px; }
</style>
</head>
<body>
<main class="canvas">

  <section class="card card-back" aria-label="Card back">
    <div class="back-mark"><span class="back-mark-name">LIMBWORKS</span></div>
    <p class="back-url">www.limbworksinc.com</p>
  </section>

  <section class="card card-front" aria-label="Card front">
    <div class="side-band">
      <div class="band-mark">LIMBWORKS</div>
      <svg class="icon" style="top:140px" viewBox="0 0 16 16" aria-hidden="true"><circle cx="8" cy="5" r="3.5"/><path d="M1 16c0-4 3-6.5 7-6.5s7 2.5 7 6.5z"/></svg>
      <svg class="icon" style="top:167px" viewBox="0 0 16 16" aria-hidden="true"><path d="M3 1l3 3-1.5 2c1 2 3 4 5 5l2-1.5 3 3-2 2C7 14 2 9 1 3z"/></svg>
      <svg class="icon" style="top:187px" viewBox="0 0 16 16" aria-hidden="true"><rect x="2" y="3" width="12" height="10" rx="1"/></svg>
      <svg class="icon" style="top:207px" viewBox="0 0 16 16" aria-hidden="true"><rect x="4" y="1" width="8" height="14" rx="1.5"/></svg>
      <svg class="icon" style="top:227px" viewBox="0 0 16 16" aria-hidden="true"><path d="M1 3h14v10H1z M1 3l7 6 7-6" stroke="#165ea8" stroke-width="1"/></svg>
      <svg class="icon" style="top:247px" viewBox="0 0 16 16" aria-hidden="true"><circle cx="8" cy="8" r="7"/></svg>
      <svg class="icon" style="top:267px" viewBox="0 0 16 16" aria-hidden="true"><path d="M8 1a5 5 0 0 1 5 5c0 4-5 9-5 9S3 10 3 6a5 5 0 0 1 5-5z"/><circle cx="8" cy="6" r="2" fill="#165ea8"/></svg>
    </div>

    <header class="company">
      <h1 class="company-name">LIMBWORKS INC.</h1>
      <p class="company-tagline">Prosthetic &amp; Orthotic Services</p>
    </header>

    <div class="contact">
      <p class="contact-name"><strong>Mara</strong> Ellison, <span class="credentials">CO LPO</span></p>
      <p class="contact-line">555.210.4800</p>
      <p class="contact-line">555.210.4819</p>
      <p class="contact-line">555-372-6614</p>
      <p class="contact-line">mellison@limbworksinc.com</p>
      <p class="contact-line">www.limbworksinc.com</p>
      <p class="contact-line">820 Harbor Ave, Lakeview, NY 10000</p>
    </div>
  </section>

</main>
</body>
</html>
```